Income Tax Business Cards - Updates

Need to update these business cards while keeping all the same wording but just update them and make them look nicer and more modern/ on brand with our brand.

Industry/Entity Type

finance

Contact Information for Business Card

we have multiple locations so will just need to easily be able to change the address and phone numbers

Colors

Designer to choose colors to be used in the design.

```html
<!DOCTYPE html>
<html lang="en">
<head>
<meta charset="utf-8">
<title>Ledgerline Financial Group – Business Card</title>
<link rel="stylesheet" href="https://fonts.googleapis.com/css2?family=Arimo:wght@400;700&family=Montserrat:wght@700;800&display=swap">
<style>
  :root {
    --backdrop: #9a9a9a;
    --brand-green: #0d502d;
    --brand-red: #c41e26;
    --white: #ffffff;
    --ink: #3a3a3a;
  }
  * { margin: 0; padding: 0; box-sizing: border-box; }
  html, body { width: 1200px; height: 1059px; overflow: hidden; }
  body { background: var(--backdrop); position: relative; font-family: "Arimo", Arial, sans-serif; }

  .card { position: absolute; border-radius: 24px; overflow: hidden; }

  /* Front */
  .card-front { left: 256px; top: 89px; width: 687px; height: 391px; background: var(--white); }
  .front-band { position: absolute; left: 0; top: 0; width: 100%; height: 139px; background: var(--brand-green); border-bottom: 3px solid var(--brand-red); }
  .front-headline { position: absolute; left: 0; right: 0; top: 32px; text-align: center; color: var(--white); font-weight: 700; font-size: 36px; letter-spacing: 0.3px; }
  .front-headline .amount { color: var(--brand-red); font-weight: 400; }
  .front-subline { position: absolute; left: 0; right: 0; top: 84px; text-align: center; color: var(--white); font-size: 16px; }
  .estimate-pill { position: absolute; left: 168px; top: 115px; width: 357px; height: 49px; border-radius: 25px; background: var(--brand-red); color: var(--white); font-weight: 700; font-size: 34px; text-align: center; line-height: 50px; }

  .brand-name { position: absolute; left: 50px; top: 240px; width: 290px; display: flex; align-items: center; gap: 12px; color: var(--brand-green); font-weight: 700; }
  .brand-dot { width: 18px; height: 18px; border-radius: 50%; background: var(--brand-red); flex: none; }
  .brand-text { font-size: 34px; line-height: 1.05; }
  .brand-text small { display: block; font-size: 14px; letter-spacing: 3px; margin-top: 4px; }

  .divider { position: absolute; left: 344px; top: 201px; width: 2px; height: 136px; background: var(--brand-red); }
  .contact { position: absolute; left: 371px; top: 212px; color: var(--ink); font-size: 19px; line-height: 25px; }
  .contact-phone { display: flex; align-items: center; gap: 6px; margin-top: 8px; color: var(--brand-green); font-weight: 700; font-size: 21px; }

  /* Back */
  .card-back { left: 253px; top: 569px; width: 694px; height: 394px; background: var(--brand-red); font-family: "Montserrat", Arial, sans-serif; }
  .back-band { position: absolute; left: 0; top: 0; width: 100%; height: 202px; background: var(--brand-green); border-bottom: 6px solid var(--white); }
  .back-line { position: absolute; left: 0; right: 0; text-align: center; font-weight: 800; line-height: 1; }
  .file-your { top: 47px; font-size: 77px; color: var(--white); }
  .taxes-here { top: 118px; font-size: 77px; color: var(--brand-red); }
  .up-to { top: 230px; font-size: 78px; color: var(--white); letter-spacing: 1px; }
  .same-day { top: 313px; font-size: 49px; color: var(--white); font-weight: 700; letter-spacing: 0.5px; }
</style>
</head>
<body>

<section class="card card-front">
  <div class="front-band"></div>
  <h1 class="front-headline">UP TO <span class="amount">&amp;6000</span> SAME DAY ADVANCE</h1>
  <p class="front-subline">ON APPROVED TAX RETURNS!</p>
  <div class="estimate-pill">FREE ESTIMATES!</div>

  <div class="brand-name">
    <span class="brand-dot"></span>
    <span class="brand-text">Ledgerline<small>FINANCIAL GROUP</small></span>
  </div>

  <div class="divider"></div>

  <address class="contact" style="font-style:normal">
    418 Maplewood Ave<br>
    Ste 1120<br>
    Country Name AB 5625
    <div class="contact-phone">
      <svg width="16" height="16" viewBox="0 0 24 24" aria-hidden="true"><path fill="#c41e26" d="M6.6 10.8a15.1 15.1 0 0 0 6.6 6.6l2.2-2.2c.3-.3.7-.4 1-.2 1.1.4 2.3.6 3.6.6.6 0 1 .4 1 1V20c0 .6-.4 1-1 1A17 17 0 0 1 3 4c0-.6.4-1 1-1h3.5c.6 0 1 .4 1 1 0 1.3.2 2.5.6 3.6.1.3 0 .7-.2 1z"/></svg>
      (555) 555-555
    </div>
  </address>
</section>

<section class="card card-back">
  <div class="back-band"></div>
  <p class="back-line file-your">FILE YOUR</p>
  <p class="back-line taxes-here">TAXES HERE</p>
  <p class="back-line up-to">UP TO &amp;6000</p>
  <p class="back-line same-day">SAME DAY ADVANCE</p>
</section>

</body>
</html>
```